MRT Property - Business Cards

Looking for a business card & general letterhead, signage etc design for our new logo.

Colours:
000a20
0056a2
00b5ef
0088ce
68cef2

Fonts:
Poppins
Karla

Please keep look and feel of new brand - example in the zip package I sent.

```html
<!DOCTYPE html>
<html lang="en">
<head>
<meta charset="UTF-8">
<title>MRT Property – Business Cards</title>
<link href="https://fonts.googleapis.com/css2?family=Poppins:wght@400;500;600;700&family=Karla:wght@400;500&display=swap" rel="stylesheet">
<style>
  :root {
    --ink: #000a20;
    --card-top: #1c2233;
    --card-bottom: #10141f;
    --royal: #0056a2;
    --cyan: #00b5ef;
    --azure: #0088ce;
    --sky: #68cef2;
    --silver: #8a8f99;
    --text: #e6e9ef;
    --muted: #b7bcc6;
    --backdrop: #1a1a1c;
  }
  * { margin: 0; padding: 0; box-sizing: border-box; }
  html, body { width: 1200px; height: 852px; overflow: hidden; }
  body {
    background: var(--backdrop);
    font-family: "Poppins", sans-serif;
    position: relative;
  }
  .card {
    position: absolute;
    width: 500px;
    height: 286px;
    border-radius: 18px;
    background: linear-gradient(160deg, var(--card-top), var(--card-bottom));
    overflow: hidden;
    box-shadow: 0 18px 40px rgba(0,0,0,0.55);
  }
  .card--front { left: 90px; top: 150px; }
  .card--back  { left: 610px; top: 416px; }

  /* Front */
  .front-brand {
    position: absolute;
    left: 0; right: 0; top: 100px;
    text-align: center;
    font-weight: 600;
    font-size: 40px;
    letter-spacing: 1px;
    color: var(--silver);
  }
  .front-brand .mark {
    display: inline-block;
    width: 18px; height: 18px;
    border-radius: 50%;
    background: var(--silver);
    margin-right: 12px;
    vertical-align: middle;
    position: relative; top: -4px;
  }
  .front-web {
    position: absolute;
    right: 28px; bottom: 30px;
    font-family: "Karla", sans-serif;
    font-size: 11px;
    letter-spacing: 4px;
    color: var(--muted);
  }
  .front-band {
    position: absolute;
    left: 0; right: 0; bottom: 0;
    height: 9px;
    background: var(--royal);
  }

  /* Back */
  .portrait {
    position: absolute;
    left: 0; top: 0;
  }
  .back-brand {
    position: absolute;
    left: 28px; top: 64px;
    font-weight: 700;
    font-size: 28px;
    color: var(--azure);
  }
  .back-brand .mark {
    display: inline-block;
    width: 12px; height: 12px;
    background: var(--azure);
    margin-right: 8px;
    vertical-align: middle;
    position: relative; top: -3px;
  }
  .address {
    position: absolute;
    right: 24px; top: 140px;
    font-size: 11px;
    color: var(--text);
  }
  .person { position: absolute; left: 28px; top: 160px; }
  .person__name { font-weight: 600; font-size: 17px; color: var(--azure); line-height: 1.1; }
  .person__role { font-size: 10px; color: var(--text); margin-top: 2px; }
  .contacts {
    position: absolute;
    left: 28px; top: 220px;
    list-style: none;
    font-size: 11px;
    color: var(--text);
  }
  .contacts li { display: flex; align-items: center; gap: 12px; height: 18px; }
  .contacts svg { width: 11px; height: 11px; fill: var(--azure); }
</style>
</head>
<body>

  <section class="card card--front" aria-label="Business card front">
    <div class="front-brand"><span class="mark"></span>MRT Property</div>
    <div class="front-web">www.mrtproperty.com</div>
    <div class="front-band"></div>
  </section>

  <section class="card card--back" aria-label="Business card back">
    <svg class="portrait" width="500" height="286" viewBox="0 0 500 286">
      <defs>
        <linearGradient id="portraitTone" x1="0" y1="0" x2="1" y2="1">
          <stop offset="0" stop-color="#2b3550"/>
          <stop offset="1" stop-color="#1a2a4a"/>
        </linearGradient>
      </defs>
      <path role="img" aria-label="Portrait photo of the associate director"
            d="M300 0 H500 V128 H300 Z" fill="url(#portraitTone)"/>
      <path d="M160 205 C235 205 240 132 300 128 H500" fill="none" stroke="var(--azure)" stroke-width="1"/>
      <line x1="28" y1="208" x2="160" y2="205" stroke="var(--azure)" stroke-width="1"/>
    </svg>

    <div class="back-brand"><span class="mark"></span>MRT Property</div>
    <div class="address">72 Harbour View Road Westmead</div>

    <div class="person">
      <div class="person__name">Declan Rourke</div>
      <div class="person__role">Associate Director</div>
    </div>

    <ul class="contacts">
      <li><svg viewBox="0 0 24 24"><path d="M6.6 10.8a15 15 0 0 0 6.6 6.6l2.2-2.2c.3-.3.7-.4 1-.2 1.1.4 2.3.6 3.6.6.6 0 1 .4 1 1V20c0 .6-.4 1-1 1A17 17 0 0 1 3 4c0-.6.4-1 1-1h3.5c.6 0 1 .4 1 1 0 1.3.2 2.5.6 3.6.1.3 0 .7-.2 1z"/></svg>555-204-7316</li>
      <li><svg viewBox="0 0 24 24"><path d="M2 5h20v14H2z M4 7v.5l8 5 8-5V7l-8 5z"/></svg>declan@mrtproperty.com</li>
      <li><svg viewBox="0 0 24 24"><circle cx="12" cy="12" r="10"/></svg>www.mrtproperty.com</li>
    </ul>
  </section>

</body>
</html>
```